New Business Card Design Project

Use the flyer uploaded and website www.brightoakbuilders.com for inspiration.
List Our Services on Backside of business cards
Marcus Delling
Harborline Builders Inc.
Licensed General Contractors
858-471-6093

Contact Information for Business Card

Use the flyer uploaded and website www.brightoakbuilders.com for inspiration. List Our Services on Backside of business cards Marcus Delling Harborline Builders Inc. Licensed General Contractors 858-471-6093

```html
<!DOCTYPE html>
<html lang="en">
<head>
<meta charset="utf-8">
<title>Harborline Builders – Business Card</title>
<link rel="stylesheet" href="https://fonts.googleapis.com/css2?family=Montserrat:wght@400;500;600;700&display=swap">
<style>
  :root {
    --backdrop: #d8d2c6;
    --card: #161616;
    --ink: #f4f4f4;
    --ink-soft: #d6d6d6;
    --rule: #cfcfcf;
  }
  * { box-sizing: border-box; margin: 0; padding: 0; }
  html, body {
    width: 900px; height: 1200px; overflow: hidden;
    background: var(--backdrop);
    font-family: "Montserrat", Arial, sans-serif;
    color: var(--ink);
  }
  .canvas { position: relative; width: 900px; height: 1200px; }
  .card {
    position: absolute; left: 80px; width: 742px; height: 442px;
    background: var(--card); border-radius: 22px;
  }
  .card--services { top: 130px; }
  .card--contact { top: 638px; }

  .brand {
    position: absolute; display: flex; align-items: center; gap: 9px;
    font-weight: 500; text-transform: uppercase; color: var(--ink); white-space: nowrap;
  }
  .brand-mark { width: 10px; height: 10px; border-radius: 50%; background: var(--ink); flex: none; }

  /* Services side */
  .card--services .brand {
    left: 0; width: 357px; justify-content: center;
    top: 274px; font-size: 16px; letter-spacing: 1.6px;
  }
  .divider { position: absolute; left: 357px; top: 108px; width: 2px; height: 263px; background: var(--rule); }
  .services { position: absolute; left: 386px; top: 104px; }
  .services h2 { font-size: 22px; font-weight: 600; margin-bottom: 10px; }
  .services ul { list-style: none; }
  .services li {
    position: relative; padding-left: 13px; font-size: 16.5px; line-height: 26.8px; color: var(--ink-soft);
  }
  .services li::before {
    content: ""; position: absolute; left: 0; top: 11px; width: 6px; height: 6px; border-radius: 50%; background: var(--ink);
  }

  /* Contact side */
  .card--contact .brand { left: 25px; top: 52px; font-size: 23px; letter-spacing: 2px; }
  .person { position: absolute; left: 38px; top: 198px; }
  .person-name { font-size: 26px; font-weight: 700; }
  .person-role { font-size: 15px; color: var(--ink-soft); margin-top: 2px; }
  .contacts { position: absolute; left: 36px; top: 288px; list-style: none; }
  .contacts li { display: flex; align-items: center; gap: 12px; height: 29px; font-size: 15.5px; color: var(--ink-soft); }
  .contacts svg { width: 15px; height: 15px; fill: var(--ink); flex: none; }
  .license { position: absolute; left: 33px; top: 393px; font-size: 15px; color: var(--ink-soft); }
</style>
</head>
<body>
<main class="canvas">
  <section class="card card--services">
    <div class="brand"><span class="brand-mark"></span>Harborline Builders</div>
    <div class="divider"></div>
    <div class="services">
      <h2>Our Services</h2>
      <ul>
        <li>Remodel: Kitchen &amp; Bath</li>
        <li>Painting: Interior &amp; Exterior</li>
        <li>Flooring: Carpet, Vinyl, Wood</li>
        <li>Window &amp; Door Replacement</li>
        <li>Plumbing: Repair &amp; Upgrades</li>
        <li>Energy Efficient Upgrades</li>
        <li>Deck &amp; Patio construction</li>
        <li>Water &amp; Mold Damage</li>
        <li>Garage Renovation</li>
      </ul>
    </div>
  </section>

  <section class="card card--contact">
    <div class="brand"><span class="brand-mark"></span>Harborline Builders</div>
    <div class="person">
      <div class="person-name">Marcus Delling</div>
      <div class="person-role">Managing Director</div>
    </div>
    <ul class="contacts">
      <li>
        <svg viewBox="0 0 16 16" aria-hidden="true"><path d="M3 1l3 3-1.5 2a9 9 0 0 0 5.5 5.5L12 10l3 3-2 2C7 15 1 9 1 3z"/></svg>
        858-471-6093
      </li>
      <li>
        <svg viewBox="0 0 16 16" aria-hidden="true"><path d="M1 3h14v1L8 9 1 4zM1 6l7 5 7-5v7H1z"/></svg>
        info@brightoakbuilders.com
      </li>
      <li>
        <svg viewBox="0 0 16 16" aria-hidden="true"><path d="M8 1a7 7 0 1 0 0 14A7 7 0 0 0 8 1zm0 1.5c1 1 1.6 2.7 1.8 4.5H6.2C6.4 5.2 7 3.5 8 2.5zM2.6 8.5h2.1c.1 1.8.6 3.3 1.4 4.4A5.5 5.5 0 0 1 2.6 8.5zm0-1.5A5.5 5.5 0 0 1 6.1 3.1C5.3 4.2 4.8 5.6 4.7 7zm5.4 6.5c-1-1-1.6-2.8-1.8-5h3.6c-.2 2.2-.8 4-1.8 5zm1.9-.6c.8-1.1 1.3-2.6 1.4-4.4h2.1a5.5 5.5 0 0 1-3.5 4.4zm1.4-5.9c-.1-1.4-.6-2.8-1.4-3.9A5.5 5.5 0 0 1 13.4 7z"/></svg>
        www.brightoakbuilders.com
      </li>
    </ul>
    <div class="license">CLSB Licensed No #2048516</div>
  </section>
</main>
</body>
</html>
```